Brookmere Osteopathy flyer

I want a clean clear DL flyer (but also want an A4 poster) promoting a new Osteopathic business in a semi rural area in Tasmania (Australia).
It can have pictures like the examples attached to show people what Osteopathy is (its like Chiropractic and physiotherapy).
I am the sole practioner and am male, so any pictures would be best to be a white male if possible.
I've attached some wording, you can use all, or none of it
I don't have a phone number for the business yet
info@brookmereosteopathy.example
www.brookmereosteopathy.example
Target Market(s)
Australians, from tradies, professionals, babies to retired people
Industry/Entity Type
Health
Look and feel

```html
<!DOCTYPE html>
<html lang="en">
<head>
<meta charset="utf-8">
<title>Brookmere Osteopathy – DL Flyers</title>
<link rel="stylesheet" href="https://fonts.googleapis.com/css2?family=Saira+Condensed:wght@600;700&family=Mulish:wght@400;500;600&family=Archivo:wght@500;600&display=swap">
<style>
  :root{
    --blue:#1589cc;
    --orange:#f39a32;
    --grey:#8e8e90;
    --grey-text:#b9b9bb;
    --ink:#222;
    --white:#fff;
    --page:#e9e9ea;
  }
  *{margin:0;padding:0;box-sizing:border-box}
  html,body{width:1200px;height:1151px;overflow:hidden;background:var(--page)}
  .flyer{position:absolute;top:84px;width:462px;height:986px;background:var(--white);overflow:hidden;box-shadow:0 2px 10px rgba(0,0,0,.15)}
  .flyer--about{left:113px}
  .flyer--reasons{left:626px}
  .brand-mark{position:absolute;left:19px;top:17px;width:113px;height:113px;border:3px solid var(--blue);border-radius:50%;display:flex;align-items:center;justify-content:center;text-align:center;font-family:"Saira Condensed",sans-serif;font-weight:700;font-size:17px;line-height:1.05;color:var(--blue);padding:12px}
  .brand-name{position:absolute;left:146px;top:35px;width:302px;font-family:"Saira Condensed",sans-serif;font-weight:700;font-size:30.5px;line-height:1;color:var(--blue);white-space:nowrap;letter-spacing:0}
  .tagline{position:absolute;left:150px;top:68px;font-family:"Saira Condensed",sans-serif;font-weight:600;font-size:31px;line-height:1;color:var(--orange);white-space:nowrap}
  .offer-band{position:absolute;top:157px;height:181px;background:var(--blue)}
  .orange-bar{position:absolute;top:348px;height:11px;background:var(--orange)}
  .offer{position:absolute;top:186px;font-family:"Saira Condensed",sans-serif;font-weight:700;color:var(--white);line-height:1}
  .offer .small{display:block;font-size:37px}
  .offer .big{display:block;font-size:64px;margin-top:2px;line-height:.92}
  .offer .mid{display:block;font-size:31px;margin-top:2px}
  .photo-circle{position:absolute;width:300px;height:300px;border-radius:50%;border:6px solid var(--white);background:radial-gradient(circle at 40% 45%,#e7d3c6 0%,#b9b3ad 40%,#6d7680 75%,#d6dde6 100%);z-index:3}
  .info-panel{position:absolute;background:var(--grey);color:var(--white);font-family:"Mulish",sans-serif}
  .service-area,.list-intro{position:absolute;font-family:"Mulish",sans-serif;font-weight:600;font-size:15px;line-height:21px;color:var(--ink)}
  .about-text{font-size:13.4px;line-height:24.5px;padding:14px 14px 0 13px}
  .photo{position:absolute;top:636px;height:167px;width:211px}
  .photo--baby{left:15px;background:linear-gradient(160deg,#8c8fa6,#6f8fb0 55%,#9aa3b8)}
  .photo--back{left:237px;background:linear-gradient(150deg,#3d5a6b,#c9a079 55%,#e6d29a)}
  .cta{position:absolute;left:0;width:100%;text-align:center;font-family:"Archivo",sans-serif;font-weight:600;font-size:20.5px;color:var(--ink)}
  .phone-box{position:absolute;left:66px;width:330px;height:57px;background:var(--blue);color:var(--white);display:flex;align-items:center;justify-content:center;gap:10px;font-family:"Archivo",sans-serif;font-weight:600;font-size:28px;letter-spacing:.5px}
  .address{position:absolute;left:0;width:100%;display:flex;align-items:center;justify-content:center;gap:14px;font-family:"Archivo",sans-serif;font-weight:600;font-size:22px;color:var(--ink)}
  .web-line{position:absolute;left:0;width:100%;top:955px;display:flex;justify-content:center;gap:12px;font-family:"Archivo",sans-serif;font-weight:500;font-size:11px;color:var(--ink)}
  .web-line span{display:flex;align-items:center;gap:5px}
  .web-line i{width:8px;height:8px;border-radius:50%;background:var(--orange);display:inline-block}
  .reasons-list{list-style:none;padding:22px 0 0 18px}
  .reasons-list li{display:flex;align-items:center;gap:16px;height:31.5px;font-size:16.5px;letter-spacing:.2px}
  .side-slogan{position:absolute;left:370px;top:310px;transform:rotate(-90deg);transform-origin:0 0;font-family:"Saira Condensed",sans-serif;font-weight:700;color:var(--grey-text);line-height:1;white-space:nowrap;z-index:4}
  .side-slogan .l1{display:block;font-size:27px}
  .side-slogan .l2{display:block;font-size:30px;font-weight:600;margin-top:4px}
</style>
</head>
<body>

<section class="flyer flyer--about">
  <div class="brand-mark">Brookmere Osteopathy</div>
  <h1 class="brand-name">BROOKMERE OSTEOPATHY</h1>
  <p class="tagline">Move Better, Feel Better.</p>

  <div class="offer-band" style="left:203px;width:259px"></div>
  <div class="orange-bar" style="left:252px;width:210px"></div>
  <div class="photo-circle" role="img" aria-label="Osteopath gently treating a woman's shoulder as she lies on a treatment table" style="left:-24px;top:137px"></div>
  <div class="offer" style="right:14px;text-align:right;z-index:4">
    <span class="small">FREE INTIAL</span>
    <span class="big">PHYSIO</span>
    <span class="mid">CONSULTATION</span>
  </div>

  <p class="service-area" style="right:14px;top:374px;text-align:right">Serving Semi Rural<br>Area In Tasmania - Australia</p>

  <div class="info-panel" style="left:0;top:424px;width:462px;height:191px">
    <p class="about-text">Brookmere Osteopathy use a tailored combination of joint mobilisa-tion/manipulation, stretching, movement, trigger point dry needling and targeted massage to reduce pain and restore optimal function. Hands-on treatment is backed up with rehabilitative exercise prescription and advice.<br>So whether you're recovering from injury or managing chronic discomfort, we're here to help you move better and feel your best.</p>
  </div>

  <div class="photo photo--baby" role="img" aria-label="Newborn baby receiving gentle cranial osteopathy"></div>
  <div class="photo photo--back" role="img" aria-label="Practitioner treating a woman's lower back"></div>

  <p class="cta" style="top:826px">Call and make an appointment today</p>
  <div class="phone-box" style="top:864px">
    <svg width="30" height="32" viewBox="0 0 30 32" fill="none" stroke="#fff" stroke-width="2"><path d="M5 4c-3 2-3 6-1 11s6 10 10 13c3 2 6 2 8 0l-4-6-3 2c-3-2-6-7-7-10l3-2-3-7z"/><path d="M17 6a6 6 0 0 1 6 6M17 1a11 11 0 0 1 11 11"/></svg>
    <span>0400 555 010</span>
  </div>
  <div class="address" style="top:938px">
    <svg width="20" height="28" viewBox="0 0 20 28"><path d="M10 0a10 10 0 0 0-10 10c0 7 10 18 10 18s10-11 10-18A10 10 0 0 0 10 0z" fill="var(--orange)"/><circle cx="10" cy="10" r="4" fill="#fff"/></svg>
    <span>48 Willow Creek Road, Brookmere</span>
  </div>
</section>

<section class="flyer flyer--reasons">
  <div class="brand-mark">Brookmere Osteopathy</div>
  <h1 class="brand-name">BROOKMERE OSTEOPATHY</h1>
  <p class="tagline">Move Better, Feel Better.</p>

  <div class="offer-band" style="left:0;width:258px"></div>
  <div class="orange-bar" style="left:0;width:208px"></div>
  <div class="photo-circle" role="img" aria-label="Osteopath gently treating a woman's shoulder as she lies on a treatment table" style="left:190px;top:137px"></div>
  <div class="offer" style="left:16px;z-index:4">
    <span class="small">FREE INTIAL</span>
    <span class="big">PHYSIO</span>
    <span class="mid">CONSULTATION</span>
  </div>

  <p class="list-intro" style="left:16px;top:373px">Common Reasons People<br>Visit An Osteopath:</p>

  <div class="info-panel" style="left:0;top:428px;width:462px;height:343px">
    <ul class="reasons-list">
      <li><svg width="20" height="14" viewBox="0 0 20 14"><path d="M1 13c1-6 6-8 12-8V1l6 6-6 6V9c-5 0-9 1-12 4z" fill="#fff"/></svg>Back / Neck Pain</li>
      <li><svg width="20" height="14" viewBox="0 0 20 14"><path d="M1 13c1-6 6-8 12-8V1l6 6-6 6V9c-5 0-9 1-12 4z" fill="#fff"/></svg>Headaches / Migraines</li>
      <li><svg width="20" height="14" viewBox="0 0 20 14"><path d="M1 13c1-6 6-8 12-8V1l6 6-6 6V9c-5 0-9 1-12 4z" fill="#fff"/></svg>Joint And Muscle Pain</li>
      <li><svg width="20" height="14" viewBox="0 0 20 14"><path d="M1 13c1-6 6-8 12-8V1l6 6-6 6V9c-5 0-9 1-12 4z" fill="#fff"/></svg>Pregnancy-related Discomfort</li>
      <li><svg width="20" height="14" viewBox="0 0 20 14"><path d="M1 13c1-6 6-8 12-8V1l6 6-6 6V9c-5 0-9 1-12 4z" fill="#fff"/></svg>Disc Related Issues</li>
      <li><svg width="20" height="14" viewBox="0 0 20 14"><path d="M1 13c1-6 6-8 12-8V1l6 6-6 6V9c-5 0-9 1-12 4z" fill="#fff"/></svg>Sciatica</li>
      <li><svg width="20" height="14" viewBox="0 0 20 14"><path d="M1 13c1-6 6-8 12-8V1l6 6-6 6V9c-5 0-9 1-12 4z" fill="#fff"/></svg>Plantar Fasciitis</li>
      <li><svg width="20" height="14" viewBox="0 0 20 14"><path d="M1 13c1-6 6-8 12-8V1l6 6-6 6V9c-5 0-9 1-12 4z" fill="#fff"/></svg>Tendonitis / Bursitis</li>
      <li><svg width="20" height="14" viewBox="0 0 20 14"><path d="M1 13c1-6 6-8 12-8V1l6 6-6 6V9c-5 0-9 1-12 4z" fill="#fff"/></svg>Adhesive Capsulitis (Frozen Shoulder)</li>
      <li><svg width="20" height="14" viewBox="0 0 20 14"><path d="M1 13c1-6 6-8 12-8V1l6 6-6 6V9c-5 0-9 1-12 4z" fill="#fff"/></svg>Tennis / Golfers Elbow</li>
    </ul>
    <p class="side-slogan"><span class="l1">BROOKMERE OSTEOPATHY</span><span class="l2">Move Better, Feel Better.</span></p>
  </div>

  <p class="cta" style="top:793px">Call and make an appointment today</p>
  <div class="phone-box" style="top:836px">
    <svg width="30" height="32" viewBox="0 0 30 32" fill="none" stroke="#fff" stroke-width="2"><path d="M5 4c-3 2-3 6-1 11s6 10 10 13c3 2 6 2 8 0l-4-6-3 2c-3-2-6-7-7-10l3-2-3-7z"/><path d="M17 6a6 6 0 0 1 6 6M17 1a11 11 0 0 1 11 11"/></svg>
    <span>0400 555 010</span>
  </div>
  <div class="address" style="top:915px">
    <svg width="20" height="28" viewBox="0 0 20 28"><path d="M10 0a10 10 0 0 0-10 10c0 7 10 18 10 18s10-11 10-18A10 10 0 0 0 10 0z" fill="var(--orange)"/><circle cx="10" cy="10" r="4" fill="#fff"/></svg>
    <span>48 Willow Creek Road, Brookmere</span>
  </div>
  <div class="web-line">
    <span><i></i>info@brookmereosteopathy.example</span>
    <span><i></i>www.brookmereosteopathy.example</span>
  </div>
</section>

</body>
</html>
```